Puffy Clouds Cotton Candy

Looking for a logo design and business cards to help a 13 year old entrepreneur promote her cotton candy business.
Contact Information for Business Card
Name, Phone & Email
Colors
E54698
E96AAD
F1A4CE
F9D9EA
FCEFF6
A7469A
B969AE
D3A5CF
EDDBEB
F8F0F9
6B429C
8869AF
B7A5CE
E3DAEB
F3F0F8
Requirements
Must have
- A fun feel that is appropriate for a teenage girl selling cotton candy

```html
<!DOCTYPE html>
<html lang="en">
<head>
<meta charset="UTF-8">
<title>Puffy Clouds Cotton Candy – Business Card</title>
<link rel="stylesheet" href="https://fonts.googleapis.com/css2?family=Poppins:wght@400;500;700&display=swap">
<style>
  :root {
    --backdrop: #fb4b9f;
    --card-pink: #e8398f;
    --card-pink-deep: #d92c82;
    --paper: #f7f7f5;
    --ink: #171726;
    --band: #000000;
    --accent: #e8398f;
    --soft-pink: #f1a4ce;
  }
  * { box-sizing: border-box; margin: 0; padding: 0; }
  html, body { width: 1200px; height: 800px; overflow: hidden; }
  body {
    background: var(--backdrop);
    font-family: "Poppins", sans-serif;
    position: relative;
  }
  .card {
    position: absolute;
    width: 520px;
    height: 297px;
    border-radius: 4px;
    overflow: hidden;
    box-shadow: 0 18px 40px rgba(150, 0, 70, 0.28);
  }
  .card-front { left: 50px; top: 252px; background: var(--paper); }
  .card-back { left: 630px; top: 252px; background: var(--card-pink); }
  .card-shapes { position: absolute; inset: 0; width: 100%; height: 100%; }

  .holder { position: absolute; left: 36px; top: 52px; }
  .holder-name {
    font-weight: 700;
    font-size: 34px;
    line-height: 1;
    color: var(--ink);
    letter-spacing: 0.5px;
  }
  .holder-rule {
    position: absolute;
    left: 150px; top: 40px;
    width: 110px; height: 1.5px;
    background: var(--accent);
  }
  .holder-role {
    margin-top: 6px;
    font-size: 9px;
    font-weight: 500;
    letter-spacing: 1.2px;
    color: var(--accent);
    text-transform: uppercase;
  }
  .contact-list {
    position: absolute;
    left: 36px; top: 118px;
    list-style: none;
    display: flex; flex-direction: column; gap: 10px;
  }
  .contact-item { display: flex; align-items: center; gap: 12px; }
  .contact-icon {
    width: 26px; height: 26px; border-radius: 50%;
    background: var(--accent);
    display: flex; align-items: center; justify-content: center;
    flex-shrink: 0;
  }
  .contact-icon svg { width: 13px; height: 13px; }
  .contact-text {
    font-size: 10px; line-height: 1.2;
    font-weight: 500; color: var(--ink);
  }

  .brand {
    position: absolute;
    display: flex; flex-direction: column; align-items: center;
    text-align: center; gap: 8px;
  }
  .brand-dot { border-radius: 50%; background: var(--soft-pink); }
  .brand-name {
    font-weight: 700;
    color: #ffffff;
    line-height: 1.1;
  }
  .card-front .brand { left: 320px; top: 78px; width: 180px; }
  .card-front .brand-dot { width: 46px; height: 46px; }
  .card-front .brand-name { font-size: 19px; }

  .card-back .brand { left: 130px; top: 78px; width: 260px; }
  .card-back .brand-dot { width: 54px; height: 54px; }
  .card-back .brand-name { font-size: 26px; }

  .faint-mark {
    position: absolute;
    right: 24px; bottom: -30px;
    width: 120px; height: 120px;
    border-radius: 50%;
    background: rgba(241, 164, 206, 0.35);
  }
</style>
</head>
<body>

  <section class="card card-front" aria-label="Business card front">
    <svg class="card-shapes" viewBox="0 0 520 297" preserveAspectRatio="none" aria-hidden="true">
      <path d="M0 238 L318 238 L334 297 L0 297 Z" fill="var(--band)"/>
      <path d="M360 0 C300 18 272 90 296 160 L344 297 L520 297 L520 0 Z" fill="var(--card-pink)"/>
    </svg>

    <div class="holder">
      <h1 class="holder-name">Maya Carter</h1>
      <p class="holder-role">Systems Engineer</p>
    </div>
    <span class="holder-rule"></span>

    <ul class="contact-list">
      <li class="contact-item">
        <span class="contact-icon">
          <svg viewBox="0 0 24 24" fill="#fff"><path d="M6.6 10.8a15 15 0 0 0 6.6 6.6l2.2-2.2c.3-.3.7-.4 1-.2 1.1.4 2.3.6 3.6.6.6 0 1 .4 1 1V20c0 .6-.4 1-1 1A17 17 0 0 1 3 4c0-.6.4-1 1-1h3.5c.6 0 1 .4 1 1 0 1.3.2 2.5.6 3.6.1.3 0 .7-.2 1z"/></svg>
        </span>
        <span class="contact-text">000 0000 0000<br>000 0000 0000</span>
      </li>
      <li class="contact-item">
        <span class="contact-icon">
          <svg viewBox="0 0 24 24" fill="none" stroke="#fff" stroke-width="2"><rect x="3" y="5" width="18" height="14" rx="2"/><path d="M3 7l9 6 9-6"/></svg>
        </span>
        <span class="contact-text">Lorem Ipsum Is Simply<br>Dummy Text</span>
      </li>
      <li class="contact-item">
        <span class="contact-icon">
          <svg viewBox="0 0 24 24" fill="#fff"><path d="M12 2a7 7 0 0 0-7 7c0 5 7 13 7 13s7-8 7-13a7 7 0 0 0-7-7zm0 9.5A2.5 2.5 0 1 1 12 6.5a2.5 2.5 0 0 1 0 5z"/></svg>
        </span>
        <span class="contact-text">Lorem Ipsum Is Simply<br>Dummy Text</span>
      </li>
    </ul>

    <div class="brand">
      <span class="brand-dot"></span>
      <p class="brand-name">Puffy Clouds Cotton Candy</p>
    </div>
  </section>

  <section class="card card-back" aria-label="Business card back">
    <svg class="card-shapes" viewBox="0 0 520 297" preserveAspectRatio="none" aria-hidden="true">
      <path d="M0 190 C30 180 52 205 70 230 C88 252 120 240 140 232 C165 228 180 260 178 297 L0 297 Z" fill="var(--paper)"/>
      <path d="M395 0 C392 28 408 44 430 40 C452 36 462 58 488 56 C505 55 515 60 520 66 L520 0 Z" fill="var(--paper)"/>
    </svg>

    <div class="brand">
      <span class="brand-dot"></span>
      <p class="brand-name">Puffy Clouds Cotton Candy</p>
    </div>

    <span class="faint-mark" role="img" aria-label="Faint brand mark decoration"></span>
  </section>

</body>
</html>
```